Harbor Crestline (Business Card Design)

Need business cards designed. Something modern, chic, and sleek. Mabye the back of the card should be the navy blue that is in the logo and then just the logo on the back.

Target Market(s)

Those in the hotel, office, and renovation industry

Contact Information for Business Card

1. Logo 2. Dorian Fenwick 3. CEO/Founder 4. Phone: (833) HarbCre / (833) 427-2731 5. Email: dorian@theharborcrestline.com 6. Website: www.theharborcrestline.com

Font styles to use
Other font styles liked:
• Look at the logo font and base the font for everything else off of that.

Colors
0054AA
0677BA
7BADD7
CADEEF
E8F1F8

Requirements
Must have
• Colors that are associated in the logo
Nice to have
• Sleek modern clean and chic design.

```html
<!DOCTYPE html>
<html lang="en">
<head>
<meta charset="utf-8">
<title>Harbor Crestline — Business Card</title>
<link rel="stylesheet" href="https://fonts.googleapis.com/css2?family=Montserrat:wght@300;400;600;700&display=swap">
<style>
  :root {
    --navy: #0b1941;
    --gold: #cfa448;
    --white: #ffffff;
    --backdrop: #f4f4f4;
    --label: #111111;
  }
  * { margin: 0; padding: 0; box-sizing: border-box; }
  html, body {
    width: 1200px;
    height: 941px;
    overflow: hidden;
  }
  body {
    position: relative;
    background: var(--backdrop);
    font-family: "Montserrat", sans-serif;
  }
  .card {
    position: absolute;
    top: 330px;
    width: 431px;
    height: 247px;
    overflow: hidden;
    box-shadow: 0 8px 10px -6px rgba(0, 0, 0, 0.35);
  }
  .card--front { left: 86px; background: var(--navy); }
  .card--back  { left: 682px; background: var(--white); }

  /* Front: brand name in the top-right field */
  .front-brand {
    position: absolute;
    right: 26px;
    top: 34px;
    color: var(--white);
    font-size: 26px;
    font-weight: 600;
    line-height: 30px;
    letter-spacing: 0.3px;
    text-align: right;
  }
  .front-accent {
    position: absolute;
    left: 356px;
    top: 130px;
    width: 16px;
    height: 16px;
    background: var(--gold);
  }

  .identity {
    position: absolute;
    left: 58px;
    top: 122px;
  }
  .identity__name {
    color: var(--gold);
    font-size: 13.5px;
    font-weight: 300;
    letter-spacing: 0.2px;
    line-height: 17px;
  }
  .identity__role {
    color: var(--white);
    font-size: 9.2px;
    font-weight: 400;
    line-height: 12px;
  }
  .contact {
    position: absolute;
    left: 58px;
    top: 163px;
    list-style: none;
  }
  .contact__item {
    display: flex;
    align-items: center;
    gap: 7px;
    color: var(--white);
    font-size: 9px;
    font-weight: 300;
    line-height: 15.5px;
  }
  .contact__item strong { font-weight: 600; }
  .contact__icon {
    width: 10px;
    height: 10px;
    flex: none;
  }

  /* Back: centred brand name */
  .brand {
    position: absolute;
    left: 0;
    right: 0;
    top: 84px;
    display: flex;
    flex-direction: column;
    align-items: center;
    gap: 14px;
  }
  .brand__mark {
    width: 14px;
    height: 14px;
    background: var(--gold);
  }
  .brand__name {
    color: var(--navy);
    font-size: 24px;
    font-weight: 700;
    letter-spacing: 0.6px;
    line-height: 28px;
  }

  .side-label {
    position: absolute;
    top: 615px;
    width: 431px;
    text-align: center;
    color: var(--label);
    font-size: 14.5px;
    font-weight: 400;
    letter-spacing: 0.3px;
  }
  .side-label--front { left: 86px; }
  .side-label--back  { left: 682px; }
</style>
</head>
<body>
  <section class="card card--front" aria-label="Card front">
    <p class="front-brand">Harbor<br>Crestline</p>
    <span class="front-accent" aria-hidden="true"></span>
    <div class="identity">
      <p class="identity__name">Dorian Fenwick</p>
      <p class="identity__role">CEO/Founder</p>
    </div>
    <ul class="contact">
      <li class="contact__item">
        <svg class="contact__icon" viewBox="0 0 12 10" aria-hidden="true">
          <rect x="0.6" y="0.6" width="10.8" height="8.8" rx="1" fill="none" stroke="var(--gold)" stroke-width="1.1"/>
          <path d="M0.9 1.2 L6 5.4 L11.1 1.2" fill="none" stroke="var(--gold)" stroke-width="1.1"/>
        </svg>
        <span>dorian@<strong>theharborcrestline.com</strong></span>
      </li>
      <li class="contact__item">
        <svg class="contact__icon" viewBox="0 0 24 24" aria-hidden="true">
          <path fill="var(--gold)" d="M6.6 10.8a15.1 15.1 0 0 0 6.6 6.6l2.2-2.2c.3-.3.7-.4 1-.2 1.1.4 2.3.6 3.6.6.6 0 1 .4 1 1V20c0 .6-.4 1-1 1A17 17 0 0 1 3 4c0-.6.4-1 1-1h3.5c.6 0 1 .4 1 1 0 1.3.2 2.5.6 3.6.1.3 0 .7-.2 1z"/>
        </svg>
        <span>(833) HarbCre / (833) 427-2731</span>
      </li>
    </ul>
  </section>

  <section class="card card--back" aria-label="Card back">
    <div class="brand">
      <span class="brand__mark" aria-hidden="true"></span>
      <span class="brand__name">Harbor Crestline</span>
    </div>
  </section>

  <p class="side-label side-label--front">FRONT</p>
  <p class="side-label side-label--back">BACK</p>
</body>
</html>
```